General Surgeon flyer to be distributed to GPs

I am a general surgeon and I would like to have a flyer designed aiming to introduce myself to GPs.

Name: Dr Tobias Lindqvar MD, FRACS
Address: Suite 4B, Brellam private hospital, 418 Corvell Parade, Halvery, VIC, 3999
T: (03) 9587 6102
F: (03) 9463 1178
E: referrals@quillfordsurgeons.com.au
Website: www.quillfordsurgeons.com.au

Tobias is a highly trained general surgeon, having completed extensive surgical training at Tarrowby health, Pellington and Corrigan Health networks. He further specialized by completing a fellowship in Oesophagogastric and Bariatric Surgery at St Aldric’s Hospital Melbourne, one of Victoria’s leading Upper GI surgical centres.

With expertise in both advanced laparoscopic and open surgical techniques, he performs a wide range of procedures involving the gastrointestinal system, abdominal wall hernias, as well as other major and minor general surgical operations. In addition to holding appointments at Tarrowby Health, he also operates at Brellam and Fernwick Private Hospitals.

Dr Lindqvar is committed to providing patient-centred care with a focus on surgical precision, safety, and long-term health outcomes.

He is also fluent in Farsi/Pesrian.
Outside of surgery, Tobias enjoys playings classical piano and spending time with his 6-year-old Bordoodle on long walks.

Upper GI & Bariatric Surgery:
Hiatus hernia repair, sleeve gastrectomy, gastric bypass
General Surgery conditions:
Gallbladder Surgery: Laparoscopic cholecystectomy
Hernia Repair: Laparoscopic and open surgery (inguinal,
umbilical, incisional)
Anorectal Procedures: Haemorrhoidectomy, haemorrhoid banding
Hand Surgery: Carpal tunnel release, Lymph Node Biopsy
Ingrown Toenail Surgery
Skin & Soft Tissue Surgery: Skin cancer removal, lipoma and
sebaceous cyst excision
Emergency Surgery: Laparotomy, Appendicectomy, bowel resection
Endoscopy: Diagnostic and therapeutic procedures

```html
<!DOCTYPE html>
<html lang="en">
<head>
<meta charset="utf-8">
<title>Dr Tobias Lindqvar – General Surgeon</title>
<link href="https://fonts.googleapis.com/css2?family=Poppins:wght@400;500;600;700&family=Roboto:wght@300;400;500;700&display=swap" rel="stylesheet">
<style>
:root{
  --stage:#0a2338;
  --paper:#ffffff;
  --blue:#0b68ad;
  --blue-deep:#0a5796;
  --cyan:#0094d8;
  --sky:#e4f3fb;
  --pill:#1d4f91;
  --ink:#3a3a3a;
  --ink-strong:#1e1e1e;
  --accent-text:#1d5aa6;
}
*{margin:0;padding:0;box-sizing:border-box}
html,body{width:1200px;height:1200px;overflow:hidden;background:var(--stage)}
.flyer{position:absolute;left:202px;top:112px;width:766px;height:992px;background:var(--paper);overflow:hidden;font-family:"Roboto",Arial,sans-serif}
.flyer-shapes{position:absolute;inset:0;width:766px;height:992px}
.brand{position:absolute;left:30px;top:58px;width:150px;text-align:center;color:var(--accent-text);font-family:"Poppins",sans-serif;font-weight:500;font-size:13px;letter-spacing:1.5px;line-height:18px}
.brand-dot{width:46px;height:46px;border-radius:50%;background:var(--accent-text);margin:0 auto 14px}
.doctor-name{position:absolute;left:50px;top:258px;color:#fff;font-family:"Poppins",sans-serif;font-weight:700;font-size:42px;line-height:42px;letter-spacing:-0.5px}
.doctor-name .credentials{font-weight:500;font-size:19px;letter-spacing:0;border-left:2px solid #fff;padding-left:10px;margin-left:6px;vertical-align:-2px}
.contact-phones{position:absolute;left:50px;top:356px;color:#fff;font-family:"Poppins",sans-serif;font-weight:600;font-size:16.5px;display:flex;gap:14px;align-items:center}
.contact-phones span{display:flex;align-items:center;gap:5px}
.address{position:absolute;left:50px;top:385px;color:#fff;font-family:"Poppins",sans-serif;font-size:13px;line-height:19px;width:260px;white-space:nowrap}
.bio{position:absolute;left:50px;top:535px;width:345px;color:var(--ink);font-weight:300;font-size:12px;line-height:15px;text-align:justify;hyphens:auto;-webkit-hyphens:auto}
.bio p{margin-bottom:10px}
.bio p.lead{margin-bottom:15px}
.bio strong{font-weight:700;color:var(--ink-strong)}
.bio .languages{color:var(--accent-text);font-weight:500;margin-bottom:0}
.web-links{position:absolute;left:50px;top:855px;font-family:"Poppins",sans-serif;font-weight:500;font-size:16px;color:var(--ink-strong);line-height:23px}
.web-links div{display:flex;align-items:center;gap:7px}
.badges{position:absolute;left:45px;top:912px;display:flex;gap:14px;align-items:center}
.badge-circle{width:40px;height:40px;border-radius:50%;background:#2ab3a0}
.badge-square{width:26px;height:34px;background:var(--pill);border-radius:2px 2px 13px 13px}
.services{position:absolute;left:445px;top:495px;width:312px}
.pill{background:var(--pill);color:#fff;font-weight:700;font-size:16.5px;height:33px;line-height:33px;padding-left:17px;border-radius:17px;margin-bottom:8px;width:300px}
.service-list{list-style:none;margin:0 0 12px 20px;color:var(--ink);font-size:13.4px;line-height:16.5px;white-space:nowrap}
.service-list li{position:relative;padding-left:19px}
.service-list li::before{content:"";position:absolute;left:2px;top:4px;width:8px;height:8px;border:1.3px solid var(--accent-text);transform:rotate(45deg)}
.service-list b{font-weight:700;color:var(--ink-strong)}
</style>
</head>
<body>
<div class="flyer">
  <svg class="flyer-shapes" viewBox="0 0 1233 1596" preserveAspectRatio="none">
    <polygon points="245,0 1233,0 1233,820 880,560 0,850 0,405 510,222" fill="var(--blue)"/>
    <g role="img" aria-label="Portrait photograph of the surgeon in a suit and tie, with a faded enlarged portrait behind">
      <polygon points="600,0 1233,0 1233,560 760,330" fill="var(--blue-deep)" opacity="0.45"/>
      <polygon points="820,70 1233,40 1233,810 1020,690 840,560" fill="#4f87be"/>
      <ellipse cx="990" cy="250" rx="130" ry="170" fill="#6a9bc8"/>
      <polygon points="800,560 1060,370 1233,460 1233,810" fill="#2c4f8a"/>
    </g>
    <polygon points="615,330 690,330 1233,770 1233,830" fill="#5cc3ef" opacity="0.7"/>
    <polygon points="683,650 880,560 1233,820 1233,1596 685,1596" fill="var(--sky)"/>
    <polygon points="660,620 880,550 1233,800 1233,820 880,580 683,650" fill="#ffffff"/>
    <polygon points="310,0 380,0 438,78 360,78" fill="var(--cyan)"/>
    <polygon points="1098,130 1175,130 1233,180 1233,250" fill="var(--cyan)"/>
    <polygon points="970,0 1110,0 1030,40" fill="#ffffff"/>
    <polygon points="0,750 78,750 140,800 60,810" fill="var(--cyan)"/>
    <polygon points="1000,1596 1233,1510 1233,1596" fill="var(--cyan)"/>
  </svg>

  <div class="brand"><div class="brand-dot"></div>QUILLFORD<br>SURGEONS</div>

  <h1 class="doctor-name">Dr Tobias<br>Lindqvar<span class="credentials">MD, FRACS</span></h1>

  <div class="contact-phones">
    <span><svg width="16" height="16" viewBox="0 0 24 24"><path fill="#fff" d="M6.6 10.8a15.1 15.1 0 0 0 6.6 6.6l2.2-2.2a1 1 0 0 1 1-.25 11.4 11.4 0 0 0 3.6.57 1 1 0 0 1 1 1V20a1 1 0 0 1-1 1A17 17 0 0 1 3 4a1 1 0 0 1 1-1h3.5a1 1 0 0 1 1 1c0 1.25.2 2.450.57 3.57a1 1 0 0 1-.25 1z"/></svg>(03) 9587 6102</span>
    <span><svg width="18" height="16" viewBox="0 0 24 22"><path fill="#fff" d="M6 0h12v6H6zM2 7h20a2 2 0 0 1 2 2v7h-5v-3H5v3H0V9a2 2 0 0 1 2-2zm5 8h10v7H7z"/></svg>(03) 9463 1178</span>
  </div>

  <p class="address">Suite 4B, Brellam private hospital, 418<br>Corvell Parade, Halvery,<br>VIC, 3999</p>

  <div class="bio">
    <p class="lead"><strong>Tobias</strong> is a highly trained general surgeon, having completed extensive surgical training at Tarrowby health, Pellington and Corrigan Health networks. He further specialized by completing a fellowship in Oesophagogastric and Bariatric Surgery at St Aldric’s Hospital Melbourne, one of Victoria’s leading Upper GI surgical centres.</p>
    <p>With expertise in both advanced laparoscopic and open surgical techniques, he performs a wide range of procedures involving the gastrointestinal system, abdominal wall hernias, as well as other major and minor general surgical operations. In addition to holding appointments at Tarrowby Health, he also operates at Brellam and Fernwick Private Hospitals.</p>
    <p>Dr Lindqvar is committed to providing patient-centred care with a focus on surgical precision, safety, and long-term health outcomes.</p>
    <p class="languages">He is also fluent in Farsi/Pesrian.</p>
    <p>Outside of surgery, Tobias enjoys playings classical piano and spending time with his 6-year-old Bordoodle on long walks.</p>
  </div>

  <div class="web-links">
    <div><svg width="17" height="12" viewBox="0 0 17 12"><rect x="0.6" y="0.6" width="15.8" height="10.8" fill="none" stroke="#1d5aa6" stroke-width="1.2"/><path d="M0.6 0.6l7.9 6 7.9-6M0.6 11.4l6-5M16.4 11.4l-6-5" fill="none" stroke="#1d5aa6" stroke-width="1.2"/></svg>referrals@quillfordsurgeons.com.au</div>
    <div><svg width="17" height="17" viewBox="0 0 20 20"><g fill="none" stroke="#1d5aa6" stroke-width="1.3"><circle cx="10" cy="10" r="8.6"/><ellipse cx="10" cy="10" rx="4" ry="8.6"/><path d="M1.4 10h17.2M3 5.5h14M3 14.5h14"/></g></svg>www.quillfordsurgeons.com.au</div>
  </div>

  <div class="badges">
    <div class="badge-circle" role="img" aria-label="Partner badge"></div>
    <div class="badge-square" role="img" aria-label="College fellowship badge"></div>
  </div>

  <section class="services">
    <h2 class="pill">Upper GI &amp; Bariatric Surgery:</h2>
    <ul class="service-list">
      <li>Hiatus hernia repair,</li>
      <li>sleeve gastrectomy</li>
      <li>gastric bypass</li>
    </ul>
    <h2 class="pill">General Surgery conditions:</h2>
    <ul class="service-list">
      <li><b>Gallbladder Surgery:</b><br>Laparoscopic cholecystectomy</li>
      <li><b>Hernia Repair:</b> Laparoscopic and open<br>surgery (inguinal,<br>umbilical, incisional)</li>
      <li><b>Anorectal Procedures:</b> Haemorrhoidectomy,<br>haemorrhoid banding</li>
      <li><b>Hand Surgery:</b> Carpal tunnel release,<br>Lymph Node Biopsy</li>
    </ul>
    <h2 class="pill">Ingrown Toenail Surgery</h2>
    <ul class="service-list">
      <li><b>Skin &amp; Soft Tissue Surgery:</b><br>Skin cancer removal, lipoma and<br>sebaceous cyst excision</li>
      <li><b>Emergency Surgery:</b> Laparotomy,<br>Appendicectomy, bowel resection</li>
      <li><b>Endoscopy:</b> Diagnostic and therapeutic<br>procedures</li>
    </ul>
  </section>
</div>
</body>
</html>
```